Letter design, envelope design, and more

Hello, we the Tavrin Gmbh are looking for our shop. Letter C5. Design does not have to be like a business card, so it can have straight lines. Only the color is important. The logo is the text under TaVRin omit.It should not be playful but Profesionel

Font styles to use
Sans Serif

Colors
0555a3
3176b5
85abd2
85cae6
34a7d8
0792cd
cee9f5
cfdfed
000000

Requirements
Must have
• Color like business card, Please, with the text under TaVRin, Correct address Lindmattstr. 4 Zip code 9517 Kelsach, as well as Couvert Without addressing only design and logo with TaVrn
Nice to have
• more writing articles
Should not have
• Not too colored, Text under TaVRin, bright colors

```html
<!DOCTYPE html>
<html lang="en">
<head>
<meta charset="utf-8">
<title>Tavrin Gmbh – Stationery</title>
<link rel="stylesheet" href="https://fonts.googleapis.com/css2?family=Source+Sans+3:wght@400;600;700&display=swap">
<style>
  :root {
    --navy: #0b1c6f;
    --steel: #7aa2bc;
    --paper: #ffffff;
    --ink: #111111;
    --backdrop: #e3e5e7;
  }
  * { margin: 0; padding: 0; box-sizing: border-box; }
  html, body { width: 1200px; height: 1127px; overflow: hidden; }
  body {
    background: var(--backdrop);
    font-family: "Source Sans 3", Arial, sans-serif;
    color: var(--ink);
    position: relative;
  }
  .item {
    position: absolute;
    background: var(--paper);
    box-shadow: 0 1px 3px rgba(0,0,0,.12);
    overflow: hidden;
  }
  .top-band { position: absolute; left: 0; top: 0; width: 100%; background: var(--navy); }
  .footer { position: absolute; left: 0; bottom: 0; width: 100%; display: block; }
  .web { font-family: "Source Sans 3", sans-serif; font-weight: 600; fill: #fff; letter-spacing: 1.4px; }

  .wordmark {
    position: absolute;
    display: flex; align-items: center;
    color: var(--navy);
    font-weight: 700;
    letter-spacing: .06em;
  }
  .wordmark .mark { background: var(--navy); margin-right: .35em; }
  .flap { position: absolute; left: 0; top: 0; display: block; }
  .flap-name { font-family: "Source Sans 3", sans-serif; font-weight: 700; fill: #fff; letter-spacing: 2px; }

  .envelope-portrait { left: 81px; top: 219px; width: 290px; height: 411px; }

  .letterhead-small { left: 401px; top: 222px; width: 290px; height: 411px; }
  .letterhead-small .top-band { height: 17px; }
  .letterhead-small .wordmark { left: 22px; top: 29px; font-size: 13px; }
  .letterhead-small .mark { width: 12px; height: 12px; }

  .letter { left: 736px; top: 123px; width: 400px; height: 564px; }
  .letter .top-band { height: 19px; }
  .letter .wordmark { left: 36px; top: 38px; font-size: 20px; }
  .letter .mark { width: 18px; height: 18px; }
  .letter-body {
    position: absolute; left: 59px; top: 153px; width: 284px;
    font-size: 7px; line-height: 8.6px; font-weight: 600;
  }
  .letter-body p { margin-bottom: 8.6px; }
  .letter-body .salutation { margin-bottom: 29px; }
  .signature {
    width: 60px; height: 32px; margin: 36px 0 6px;
    background: linear-gradient(90deg, rgba(0,0,0,.08), rgba(0,0,0,.02));
  }
  .signer { line-height: 12px; font-size: 8px; font-weight: 400; }
  .contacts {
    position: absolute; left: 29px; bottom: 19px;
    display: flex; gap: 16px; font-size: 5.5px; font-weight: 700; align-items: center;
  }
  .contacts span { display: flex; align-items: center; gap: 2px; }
  .contacts svg { width: 6px; height: 6px; }

  .envelope-landscape { left: 163px; top: 732px; width: 411px; height: 290px; }

  .letterhead-wide { left: 606px; top: 732px; width: 408px; height: 290px; }
  .letterhead-wide .top-band { height: 18px; }
  .letterhead-wide .wordmark { left: 27px; top: 34px; font-size: 17px; }
  .letterhead-wide .mark { width: 15px; height: 15px; }
</style>
</head>
<body>

<div class="item envelope-portrait">
  <svg class="flap" width="290" height="60" viewBox="0 0 290 60">
    <path d="M0 0H290L277 44Q272 59 256 59H34Q18 59 13 44Z" fill="var(--navy)"/>
    <text class="flap-name" x="145" y="35" text-anchor="middle" font-size="14">TAVRIN</text>
  </svg>
</div>

<div class="item letterhead-small">
  <div class="top-band"></div>
  <div class="wordmark"><span class="mark"></span>TAVRIN</div>
  <svg class="footer" width="290" height="23" viewBox="0 0 290 23">
    <rect x="0" y="10" width="204" height="13" fill="var(--steel)"/>
    <polygon points="209,0 290,0 290,23 201,23" fill="var(--navy)"/>
    <text class="web" x="248" y="13" text-anchor="middle" font-size="6">www.tavrin.ch</text>
  </svg>
</div>

<div class="item letter">
  <div class="top-band"></div>
  <div class="wordmark"><span class="mark"></span>TAVRIN</div>
  <div class="letter-body">
    <p class="salutation">Dear Mr. Keller,</p>
    <p>Lorem ipsum dolor sit amet, consectetur adipiscing elit. Cras elementum eget sem quis tincidunt. Suspendisse congue accumsan ipsum ac auctor.</p>
    <p>Fusce sagittis tellus a urna ornare eleifend. Interdum et malesuada fames ac ante ipsum primis in faucibu. Fusce pulvinar sodales diam et consequat. Praesent placerat nulla vitae nisl ullamcorper, vel facilisis lorem consequat. Fusce sagittis tellus a urna ornare eleifend. Interdum et malesuada fames ac ante ipsum primis in faucibu. Fusce pulvinar sodales diam et consequat. Praesent placerat nulla vitae nisl ullamcorper, vel facilisis lorem consequat.</p>
    <p>Fusce sagittis tellus a urna ornare eleifend. Interdum et malesuada fames ac ante ipsum primis in faucibu. Fusce pulvinar sodales diam et consequat. Praesent placerat nulla vitae nisl ullamcorper, vel facilisis lorem consequat.</p>
    <p>Lorem ipsum dolor sit amet, consectetur adipiscing elit. Cras elementum eget sem quis tincidunt.</p>
    <div class="signature" role="img" aria-label="Handwritten signature"></div>
    <div class="signer">Lukas Brenner<br>Co Founder &amp; CEO</div>
  </div>
  <div class="contacts">
    <span><svg viewBox="0 0 10 10"><path d="M2 1l2 2-1 1.5q1 2 2.5 2.5L7 6l2 2-1.5 1.5Q3 9 .5 2.5Z" fill="none" stroke="#111" stroke-width="1"/></svg>+41 71 555 20 40</span>
    <span><svg viewBox="0 0 10 10"><rect x=".5" y="2" width="9" height="6" fill="none" stroke="#111"/><path d="M.5 2l4.5 3.5L9.5 2" fill="none" stroke="#111"/></svg>info@tavrin.ch</span>
    <span><svg viewBox="0 0 10 10"><path d="M5 9.5Q1.5 5.5 1.5 3.5a3.5 3.5 0 017 0Q8.5 5.5 5 9.5Z" fill="none" stroke="#111"/><circle cx="5" cy="3.5" r="1.2" fill="#111"/></svg>Lindmattstr. 4 | 9517 Kelsach</span>
  </div>
  <svg class="footer" width="400" height="26" viewBox="0 0 400 26">
    <rect x="0" y="15" width="293" height="11" fill="var(--steel)"/>
    <polygon points="300,0 400,0 400,26 288,26" fill="var(--navy)"/>
    <text class="web" x="348" y="16" text-anchor="middle" font-size="7">www.tavrin.ch</text>
  </svg>
</div>

<div class="item envelope-landscape">
  <svg class="flap" width="411" height="60" viewBox="0 0 411 60">
    <path d="M0 0H411L396 43Q390 59 372 59H56Q38 59 31 43Z" fill="var(--navy)"/>
    <text class="flap-name" x="205" y="35" text-anchor="middle" font-size="14">TAVRIN</text>
  </svg>
</div>

<div class="item letterhead-wide">
  <div class="top-band"></div>
  <div class="wordmark"><span class="mark"></span>TAVRIN</div>
  <svg class="footer" width="408" height="23" viewBox="0 0 408 23">
    <rect x="0" y="11" width="305" height="12" fill="var(--steel)"/>
    <polygon points="313,0 408,0 408,23 302,23" fill="var(--navy)"/>
    <text class="web" x="358" y="13" text-anchor="middle" font-size="6.5">www.tavrin.ch</text>
  </svg>
</div>

</body>
</html>
```